Harborline Renewal Business Card Design

Professional and clean design. The design colors should flow with the logo. Two-sided card with the website on the back which is:

www.HarborlineRenewal.example.

"Specializing in Water Damage Restoration"

On the front I need the name, email, phone, and logo.

Name: Darnell Quisby
Email: Darnell@HarborlineRenewal.example
Phone: 555-318-2046 for now

I only have the Preview and Thumbnail right now but should have the source files uploaded within a day or two.

Target Market(s)

Flood victims, home owners with water damage from busted pipes etc...

Industry/Entity Type

Business

Contact Information for Business Card

Name: Darnell Quisby

Font styles to use
Serif
Sans Serif

Requirements
Must have
• Business Card Details Info

```html
<!DOCTYPE html>
<html lang="en">
<head>
<meta charset="utf-8">
<title>Harborline Renewal — Business Card</title>
<link rel="stylesheet" href="https://fonts.googleapis.com/css2?family=Open+Sans:ital,wght@0,400;0,600;0,700;1,400&display=swap">
<style>
  :root {
    --brand-blue: #2a98d8;
    --brand-deep: #1f86c7;
    --brand-light: #5cc3ee;
    --ink-grey: #6b6b6b;
    --card-white: #ffffff;
    --backdrop: #e9e7e3;
  }
  * { box-sizing: border-box; margin: 0; padding: 0; }
  html, body {
    width: 1200px; height: 950px; overflow: hidden;
    background: var(--backdrop);
    font-family: "Open Sans", Arial, sans-serif;
  }
  .stage { position: relative; width: 1200px; height: 950px; }
  .card {
    position: absolute; left: 250px; width: 700px; height: 400px;
    overflow: hidden; border-radius: 4px;
    box-shadow: 0 10px 26px rgba(0,0,0,0.22);
  }
  /* Back side */
  .card-back { top: 60px; background: var(--brand-blue); }
  .back-mark {
    position: absolute; left: 0; right: 0; top: 150px;
    display: flex; align-items: center; justify-content: center; gap: 14px;
    color: var(--card-white); font-weight: 600; font-size: 30px; letter-spacing: 1px;
  }
  .back-mark .dot {
    width: 44px; height: 44px; border-radius: 50%; background: var(--card-white);
  }
  .tagline {
    position: absolute; left: 0; right: 0; top: 240px; text-align: center;
    color: var(--card-white); font-style: italic; font-size: 19px;
  }
  /* Front side */
  .card-front { top: 490px; background: var(--card-white); }
  .front-decor { position: absolute; left: -120px; top: -40px; }
  .front-info {
    position: absolute; right: 40px; top: 60px; text-align: right;
  }
  .wordmark {
    display: flex; align-items: center; justify-content: flex-end; gap: 12px;
    color: var(--brand-deep); font-weight: 600; font-size: 30px; letter-spacing: 1px;
  }
  .wordmark .dot { width: 40px; height: 40px; border-radius: 50%; background: var(--brand-blue); }
  .person {
    margin-top: 44px; color: var(--brand-deep); font-weight: 700; font-size: 26px;
  }
  .contact-list { list-style: none; margin-top: 10px; }
  .contact-list li {
    display: flex; align-items: center; justify-content: flex-end; gap: 10px;
    color: var(--ink-grey); font-size: 19px; line-height: 32px;
  }
  .contact-list svg { width: 18px; height: 18px; flex: none; }
</style>
</head>
<body>
<main class="stage">
  <section class="card card-back" aria-label="Card back">
    <div class="back-mark"><span class="dot"></span><span>Harborline Renewal</span></div>
    <p class="tagline">Specializing in Water Damage Restoration</p>
  </section>

  <section class="card card-front" aria-label="Card front">
    <svg class="front-decor" width="420" height="420" viewBox="0 0 420 420" aria-hidden="true">
      <defs>
        <linearGradient id="decorFill" x1="0" y1="0" x2="0" y2="1">
          <stop offset="0" stop-color="#2a98d8"/>
          <stop offset="1" stop-color="#5cc3ee"/>
        </linearGradient>
      </defs>
      <circle cx="210" cy="210" r="200" fill="url(#decorFill)"/>
    </svg>

    <div class="front-info">
      <div class="wordmark"><span class="dot"></span><span>Harborline Renewal</span></div>
      <p class="person">Darnell Quisby</p>
      <ul class="contact-list">
        <li>555-318-2046 for now
          <svg viewBox="0 0 20 20" aria-hidden="true"><circle cx="10" cy="10" r="10" fill="#2a98d8"/><path d="M6.5 5.5l2 0 1 3-1.3 1a6 6 0 0 0 2.8 2.8l1-1.3 3 1v2c0 .6-.5 1-1 1A9 9 0 0 1 5.5 6.5c0-.5.4-1 1-1z" fill="#fff"/></svg>
        </li>
        <li>Darnell@HarborlineRenewal.example
          <svg viewBox="0 0 20 20" aria-hidden="true"><circle cx="10" cy="10" r="10" fill="#2a98d8"/><rect x="5" y="6.5" width="10" height="7" fill="#fff"/><path d="M5 6.5l5 4 5-4" fill="none" stroke="#2a98d8" stroke-width="1.2"/></svg>
        </li>
        <li>www.HarborlineRenewal.example
          <svg viewBox="0 0 20 20" aria-hidden="true"><circle cx="10" cy="10" r="10" fill="#2a98d8"/><circle cx="10" cy="10" r="5" fill="none" stroke="#fff" stroke-width="1.3"/><path d="M5 10h10M10 5c-2.5 3-2.5 7 0 10M10 5c2.5 3 2.5 7 0 10" fill="none" stroke="#fff" stroke-width="1"/></svg>
        </li>
      </ul>
    </div>
  </section>
</main>
</body>
</html>
```